Business Card front and back

I am looking for business card design. I really really like the design file I uploaded named 627788_19250069_3478263_85f427ee_image

Target Market(s)

Corporate Fitness High end Private country club

Industry/Entity Type

Fitness Industry

Contact Information for Business Card

The last image I like as an example I uploaded a bunch of my logos. The file labeled "the signature" is my business card information for you to use

Colors
0054AA
0677BA
7BADD7
CADEEF
E8F1F8

Requirements
Must have
• E-mail sigThe file I uploaded labeled "627788_19250069_3478263_85f427ee_image" with all the plus signs on the back if those could be the logo symbol I uploaded labeled "1 back.png"

```html
<!DOCTYPE html>
<html lang="en">
<head>
<meta charset="utf-8">
<title>Peak Form Studio – Business Card</title>
<link href="https://fonts.googleapis.com/css2?family=Orbitron:wght@700&family=Ubuntu:wght@400;500&display=swap" rel="stylesheet">
<style>
  :root {
    --backdrop: #1c1c1c;
    --card-dark: #2f2f30;
    --card-white: #ffffff;
    --brand-blue: #447ec2;
    --ink-dark: #2b2b2c;
    --text-light: #ffffff;
    --pattern-light: #8a8a8c;
    --pattern-mid: #3a3a3b;
    --pattern-deep: #0c0c0d;
  }
  * { margin: 0; padding: 0; box-sizing: border-box; }
  html, body { width: 1200px; height: 1015px; overflow: hidden; }
  body {
    background: var(--backdrop);
    font-family: "Ubuntu", sans-serif;
    position: relative;
  }
  .card {
    position: absolute;
    left: 240px;
    width: 720px;
    height: 411px;
    overflow: hidden;
    box-shadow: 0 18px 40px rgba(0,0,0,.55);
  }
  /* Back */
  .card-back { top: 60px; background: var(--card-dark); }
  .back-pattern {
    position: absolute; inset: 0;
    background:
      linear-gradient(215deg, var(--pattern-light) 0%, var(--pattern-mid) 42%, var(--card-dark) 58%, var(--pattern-deep) 100%);
  }
  .back-wordmark {
    position: absolute; left: 0; right: 0; top: 178px;
    display: flex; align-items: center; justify-content: center; gap: 14px;
  }
  .wordmark-square { width: 26px; height: 26px; background: var(--brand-blue); flex: none; }
  .back-wordmark .wordmark-text {
    font-family: "Orbitron", sans-serif; font-weight: 700;
    font-size: 30px; letter-spacing: 2px; color: var(--text-light);
  }
  /* Front */
  .card-front { top: 524px; background: var(--card-white); }
  .front-wordmark {
    position: absolute; left: 44px; top: 112px;
    display: flex; align-items: center; gap: 14px;
  }
  .front-wordmark .wordmark-text {
    font-family: "Orbitron", sans-serif; font-weight: 700;
    font-size: 30px; letter-spacing: 1.5px; color: var(--ink-dark);
  }
  .portrait {
    position: absolute; left: 500px; top: 30px;
    width: 192px; height: 186px;
    border: 2px solid var(--brand-blue);
    background: radial-gradient(circle at 50% 40%, #5a5a5c 0%, #2a2a2b 70%, #1d1d1e 100%);
    z-index: 2;
  }
  .band-dark {
    position: absolute; left: 0; right: 0; top: 236px; height: 106px;
    background: var(--card-dark);
  }
  .band-blue {
    position: absolute; left: 0; right: 0; top: 342px; height: 69px;
    background: var(--brand-blue);
    display: flex; align-items: center; justify-content: space-between;
    padding: 0 44px; color: var(--text-light);
  }
  .contact-list {
    position: absolute; left: 44px; top: 26px;
    list-style: none; color: var(--text-light); font-size: 19px;
  }
  .contact-list li { display: flex; align-items: center; gap: 12px; margin-bottom: 10px; }
  .icon { width: 20px; height: 20px; flex: none; }
  .person {
    position: absolute; right: 28px; top: 20px; text-align: right;
  }
  .person-name {
    font-family: "Orbitron", sans-serif; font-weight: 700;
    font-size: 26px; letter-spacing: 1px; color: var(--brand-blue);
  }
  .person-role { color: var(--text-light); font-size: 18px; margin-top: 4px; }
  .region { display: flex; align-items: center; gap: 12px; font-size: 19px; letter-spacing: 1px; }
  .website { font-size: 19px; }
</style>
</head>
<body>

<section class="card card-back" aria-label="Business card back">
  <div class="back-pattern" role="img" aria-label="Repeating pattern of the brand symbol in graded greys, light at top right fading to black at bottom left"></div>
  <div class="back-wordmark">
    <span class="wordmark-square"></span>
    <span class="wordmark-text">PEAK FORM STUDIO</span>
  </div>
</section>

<section class="card card-front" aria-label="Business card front">
  <div class="front-wordmark">
    <span class="wordmark-square"></span>
    <span class="wordmark-text">PEAK FORM STUDIO</span>
  </div>

  <div class="portrait" role="img" aria-label="Portrait photograph of the consultant"></div>

  <div class="band-dark">
    <ul class="contact-list">
      <li>
        <svg class="icon" viewBox="0 0 24 24" aria-hidden="true"><path fill="#447ec2" d="M6.6 10.8a15.1 15.1 0 0 0 6.6 6.6l2.2-2.2c.3-.3.7-.4 1-.2 1.1.4 2.3.6 3.6.6.6 0 1 .4 1 1V20c0 .6-.4 1-1 1A17 17 0 0 1 3 4c0-.6.4-1 1-1h3.5c.6 0 1 .4 1 1 0 1.3.2 2.5.6 3.6.1.3 0 .7-.2 1z"/></svg>
        555-014-2837
      </li>
      <li>
        <svg class="icon" viewBox="0 0 24 24" aria-hidden="true"><path fill="#447ec2" d="M2 5h20v14H2z"/><path fill="none" stroke="#2f2f30" stroke-width="1.6" d="M2 5l10 8 10-8"/></svg>
        dane@peakformstudio.co
      </li>
    </ul>
    <div class="person">
      <div class="person-name">DANE MORROW</div>
      <div class="person-role">Consultant</div>
    </div>
  </div>

  <div class="band-blue">
    <span class="region">
      <svg class="icon" viewBox="0 0 24 24" aria-hidden="true"><path fill="#ffffff" d="M12 2a7 7 0 0 0-7 7c0 5 7 13 7 13s7-8 7-13a7 7 0 0 0-7-7zm0 9.5A2.5 2.5 0 1 1 12 6.5a2.5 2.5 0 0 1 0 5z"/></svg>
      OR.WA.ID.MT.NV
    </span>
    <span class="website">www.peakformstudio.co</span>
  </div>
</section>

</body>
</html>
```